Business Card Design

I need business cards designed for a new company i have started that makes cakes, particularly themed kids cakes with a really modern design and I would like to have my business cards reflect this. I have attached some photos of cakes I have made and would like some to be used.

Industry/Entity Type

Business

Contact Information for Business Card

Business Name: Tarts and Treats by Maren
Mobile: 0492 815 063
email: maren@tartsandtreatsbymaren.example.au
Instagram: instagram.com/tartsandtreatsbymaren/
Facebook: fb.me/tartsandtreatsbymaren

Colors
e667a6
b768aa
3276b5

Requirements
Must have
• Business Name: Tarts and Treats by Maren
• Mobile: 0492 815 063
• email: maren@tartsandtreatsbymaren.example.au
• Instagram: instagram.com/tartsandtreatsbymaren/
• Facebook: fb.me/tartsandtreatsbymaren
Nice to have
• 2 to 3 pictures of my cakes

```html
<!DOCTYPE html>
<html lang="en">
<head>
<meta charset="utf-8">
<title>Tarts and Treats by Maren – Business Cards</title>
<link rel="stylesheet" href="https://fonts.googleapis.com/css2?family=Open+Sans:wght@400;600;700&display=swap">
<style>
  :root {
    --pink: #e667a6;
    --pink-deep: #d94f96;
    --pink-light: #f2a6cb;
    --mauve: #b768aa;
    --blue: #3276b5;
    --ink: #4a4a4a;
    --white: #ffffff;
    --backdrop: #ece9e6;
  }
  * { box-sizing: border-box; margin: 0; padding: 0; }
  html, body {
    width: 1200px; height: 950px; overflow: hidden;
    background: var(--backdrop);
    font-family: "Open Sans", Arial, sans-serif;
  }
  .sheet {
    width: 1200px; height: 950px;
    display: flex; flex-direction: column; align-items: center; justify-content: center;
    gap: 30px;
  }
  .card {
    position: relative;
    width: 750px; height: 430px;
    border-radius: 4px;
    overflow: hidden;
    box-shadow: 0 4px 14px rgba(0,0,0,.12);
  }

  /* Front */
  .card--front { background: var(--white); }
  .front__band {
    position: absolute; left: 0; right: 0; top: 170px; height: 100px;
    background: linear-gradient(90deg, var(--pink-deep) 0%, var(--pink) 55%, var(--pink-light) 100%);
  }
  .front__brand {
    position: absolute; right: 60px; top: 62px;
    display: flex; align-items: center; gap: 14px;
  }
  .brand-dot {
    width: 18px; height: 18px; border-radius: 50%; background: var(--pink);
  }
  .brand-name {
    font-size: 34px; font-weight: 600; color: var(--pink);
    letter-spacing: .2px;
  }
  .front__person {
    position: absolute; left: 48px; top: 190px; color: var(--white);
  }
  .person-name { font-size: 28px; font-weight: 600; letter-spacing: 1px; text-transform: uppercase; }
  .person-role { font-size: 17px; font-weight: 400; margin-top: 2px; }
  .front__contacts {
    position: absolute; right: 48px; top: 300px;
    display: flex; flex-direction: column; align-items: flex-end; gap: 12px;
    color: var(--ink); font-size: 16px;
  }
  .contact-row { display: flex; gap: 22px; }
  .contact { display: flex; align-items: center; gap: 7px; white-space: nowrap; }
  .contact-icon { width: 16px; height: 16px; flex: none; }
  .contact-mark {
    width: 14px; height: 14px; border-radius: 2px; background: var(--pink); flex: none;
  }

  /* Back */
  .card--back {
    background: var(--pink);
    display: flex; align-items: center; justify-content: center;
  }
  .back__brand { display: flex; align-items: center; gap: 18px; }
  .back__brand .brand-dot { width: 24px; height: 24px; background: var(--white); }
  .back__brand .brand-name { color: var(--white); font-size: 44px; }
</style>
</head>
<body>
<main class="sheet">
  <section class="card card--front" aria-label="Business card front">
    <div class="front__band"></div>
    <div class="front__brand">
      <span class="brand-dot"></span>
      <span class="brand-name">Tarts and Treats by Maren</span>
    </div>
    <div class="front__person">
      <p class="person-name">Jonas Hale</p>
      <p class="person-role">CEO/Founder</p>
    </div>
    <div class="front__contacts">
      <div class="contact-row">
        <span class="contact">
          <svg class="contact-icon" viewBox="0 0 16 16" aria-hidden="true">
            <rect x="4" y="1" width="8" height="14" rx="1.5" fill="none" stroke="#e667a6" stroke-width="1.6"/>
            <circle cx="8" cy="12.5" r="0.9" fill="#e667a6"/>
          </svg>
          0492 815 063
        </span>
        <span class="contact">
          <svg class="contact-icon" viewBox="0 0 16 16" aria-hidden="true">
            <rect x="1" y="3" width="14" height="10" rx="1" fill="#e667a6"/>
            <path d="M1.5 3.8 8 9l6.5-5.2" fill="none" stroke="#fff" stroke-width="1.3"/>
          </svg>
          maren@tartsandtreatsbymaren.example.au
        </span>
      </div>
      <div class="contact-row">
        <span class="contact"><span class="contact-mark"></span>tartsandtreatsbymaren</span>
        <span class="contact"><span class="contact-mark"></span>tartsandtreatsbymaren</span>
      </div>
    </div>
  </section>

  <section class="card card--back" aria-label="Business card back">
    <div class="back__brand">
      <span class="brand-dot"></span>
      <span class="brand-name">Tarts and Treats by Maren</span>
    </div>
  </section>
</main>
</body>
</html>
```